Animal Eye Clinic needs a Business card

We are a new veterinary ophthalmology practice (Ridgeline Pet Vision Care) and we need a business card designed. We only see animal eyes - we are not a regular veterinary clinic. We already have a logo. We are looking for a professional, good looking business card to hand out to our clients. We are looking for something simple but professional and contemporary. Our logo is likely the only picture/graphic that needs to be on the card.
Updates

Contact Information for Business Card

Delia Vossman, BSc, DVM, MSc, DipACVO
Veterinary Ophthalmologist

Phone: 250.418.3927
Email: ridgelinepetvisioncare@mailbox-example.net
Website: ridgelinepetvisioncare-example.net
Address: 1874 Thornbury Rd
Kelowna, BC, V1X 4M9

Colors

Designer to choose colors to be used in the design.

Requirements
Must have
• Our logo (attached)

```html
<!DOCTYPE html>
<html lang="en">
<head>
<meta charset="utf-8">
<title>Ridgeline Pet Vision Care – Business Card</title>
<link rel="stylesheet" href="https://fonts.googleapis.com/css2?family=Roboto:wght@400;500;700&display=swap">
<style>
  :root {
    --teal: #13909c;
    --card-white: #fbfbfa;
    --card-dark: #4a4b4d;
    --text-light: #f2f2f2;
    --emboss-hi: #56575a;
    --emboss-lo: #3f4042;
    --backdrop: #e6e6e4;
  }
  * { margin: 0; padding: 0; box-sizing: border-box; }
  html, body { width: 1200px; height: 847px; overflow: hidden; }
  body {
    background: var(--backdrop);
    font-family: "Roboto", Arial, sans-serif;
    display: flex;
    align-items: center;
    justify-content: center;
    gap: 40px;
  }
  .card {
    width: 540px;
    height: 309px;
    position: relative;
    overflow: hidden;
    border-bottom: 4px solid var(--teal);
    box-shadow: 0 6px 18px rgba(0,0,0,0.18);
  }
  .card--front {
    background: var(--card-white);
    display: flex;
    align-items: center;
    justify-content: center;
  }
  .brand {
    display: flex;
    align-items: center;
    gap: 12px;
  }
  .brand__dot {
    width: 34px; height: 34px;
    border-radius: 50%;
    background: var(--teal);
    flex: none;
  }
  .brand__name {
    color: var(--teal);
    font-weight: 500;
    font-size: 22px;
    letter-spacing: 0.04em;
    text-transform: uppercase;
  }
  .card--back { background: var(--card-dark); color: var(--text-light); }
  .card--back .brand { position: absolute; left: 30px; top: 28px; gap: 9px; }
  .card--back .brand__dot { width: 24px; height: 24px; }
  .card--back .brand__name { font-size: 15px; }
  .contact {
    position: absolute;
    left: 30px;
    top: 82px;
    width: 300px;
  }
  .contact__name {
    color: var(--teal);
    font-weight: 700;
    font-size: 19px;
    letter-spacing: 0.05em;
    text-transform: uppercase;
  }
  .contact__creds { color: var(--teal); font-size: 12px; margin-top: 3px; }
  .contact__role { font-size: 13px; margin-top: 3px; }
  .contact__address { font-size: 13px; line-height: 1.4; margin-top: 16px; }
  .contact__list { list-style: none; margin-top: 10px; font-size: 12px; line-height: 1.6; }
  .contact__list li { display: flex; align-items: center; gap: 6px; white-space: nowrap; }
  .contact__list svg { width: 11px; height: 11px; flex: none; fill: var(--teal); }
  .emboss-art {
    position: absolute;
    right: 0; bottom: 0;
    width: 230px; height: 220px;
    border-radius: 110px 0 0 0;
    background: radial-gradient(circle at 40% 35%, var(--emboss-hi), var(--emboss-lo) 75%);
  }
</style>
</head>
<body>
  <section class="card card--front">
    <div class="brand">
      <span class="brand__dot"></span>
      <span class="brand__name">Ridgeline Pet Vision Care</span>
    </div>
  </section>

  <section class="card card--back">
    <div class="brand">
      <span class="brand__dot"></span>
      <span class="brand__name">Ridgeline Pet Vision Care</span>
    </div>
    <div class="contact">
      <p class="contact__name">Delia Vossman</p>
      <p class="contact__creds">BSc, DVM, MSc, DipACVO</p>
      <p class="contact__role">Veterinary Ophthalmologist</p>
      <p class="contact__address">1874 Thornbury Rd<br>Kelowna, BC, V1X 4M9</p>
      <ul class="contact__list">
        <li><svg viewBox="0 0 24 24"><path d="M6.6 10.8a15 15 0 0 0 6.6 6.6l2.2-2.2c.3-.3.7-.4 1-.2 1.1.4 2.3.6 3.6.6.6 0 1 .4 1 1V20c0 .6-.4 1-1 1C10.6 21 3 13.4 3 4c0-.6.4-1 1-1h3.5c.6 0 1 .4 1 1 0 1.3.2 2.5.6 3.6.1.3 0 .7-.2 1z"/></svg>250.418.3927</li>
        <li><svg viewBox="0 0 24 24"><path d="M2 5h20v14H2z M2 5l10 8 10-8" /></svg>ridgelinepetvisioncare@mailbox-example.net</li>
        <li><svg viewBox="0 0 24 24"><circle cx="12" cy="12" r="10"/></svg>ridgelinepetvisioncare-example.net</li>
      </ul>
    </div>
    <div class="emboss-art" role="img" aria-label="Blind-embossed illustration of a horse, cat and dog in profile"></div>
  </section>
</body>
</html>
```